Quill Press Oceania needs a website

We require a website design which will be different to the normal websites that you visit. The objective of this website will be a call to action on the last page which will link to our email address so customers can email us their quotation requirements.

An example of how we envisage the look and the pages turning is as a flip books for example: https://www.vidharbor.example/watch?v=KtLmPzQa7Rw&feature=vh.be

page 1: just has our logo on it with the tag "Specialist producing quality printed books to your deadline."

Page 2: Black Page with white text "Black and White Book"
These are produced either digitally or offset on a complete range of stocks

Page 3: Colour books (use an image of your choice) These are also produced either digitally or offset plus we have the choice of web presses for larger print runs

Page 4: Digital books We do have a minimum run of 50 books using this process so a one off Thesis is not economically viable using this process. In special circumstance the digital process can produce books more quickly then by using our offset printing process.

Page 5: Having the complete range of printing machines at our disposal enables you to make a perfectly informed choice for your special project.

Then we need a special quote button which takes them directly to our email link. On this page we also need to add: We have had 25 years' experience printing books saving customers time and money whilst guaranteeing quality

Page 6: Logo repeated from page one with name: Morgan Elsworth and mobile phone no 0487 552 314

- Must follow the brief exactly. Must have a turn page book. Clear, simple and concise with a touch of creative flare and must lead into a call for action which is there quotation. A unique button for quotation link...something out of the ordinary which makes someone want to get a quote.

- It would be nice to have 3D Logo on Page 1 & 6.
a unique button for quotation link...something that make someone eager to proceed.

Our main objective is that they should not leave our website without giving us a quote. Please make sure that the spelling is correct and we do not require clip art images. Continue the logo colours through the theme
Updates

here is another example www.vidharbor.example/watch?v=JbXo412TrGe Added Saturday, May 13, 2017

Target Market(s)

Schools, Universities, Self Publishers, Publishers, Graphic Designers, Conference Providers, Businesses, Corporations, Government.

Industry/Entity Type

Printing

Coding

Coded - Design and coding required

Number of Pages Required

5+ page

Font styles to use
Sans Serif

Colors
34a6d7
ec1f27
fbed22
9bcb3c
ffc214
6b449b

Requirements
Must have
• Must follow the brief exactly. Must have a turn page book. Clear, simple and concise with a touch of creative flare and must lead into a call for action which is there quotation. A unique button for quotation link...something out of the ordinary which makes someone want to get a quote. would like to see the colours of the logo use throughout
Nice to have
• 3D Logo on Page 1 & 6.
• a unique button for quotation link...something that make someone eager to proceed.
• Our main objective is that they should not leave our website without giving us a quote
Should not have
• Spelling mistakes, clip art, ordinary design

```html
<!DOCTYPE html>
<html lang="en">
<head>
<meta charset="utf-8">
<title>Quill Press Oceania</title>
<link rel="stylesheet" href="https://fonts.googleapis.com/css2?family=Nunito:wght@400&display=swap">
<style>
  :root {
    --orange: #f68b1f;
    --blue: #1d6a9a;
    --red: #a61d24;
    --purple: #82648f;
    --green: #5fa843;
    --ink: #111111;
    --muted: #8a8a8a;
    --paper: #ffffff;
  }
  html, body {
    margin: 0;
    padding: 0;
    overflow: hidden;
    background: var(--paper);
  }
  .page {
    position: relative;
    width: 720px;
    height: 1200px;
    overflow: hidden;
    background: var(--paper);
    font-family: "Nunito", sans-serif;
  }
  .page-art {
    position: absolute;
    inset: 0;
  }
  .brand {
    position: absolute;
    top: 272px;
    left: 176px;
    width: 400px;
    text-align: center;
    margin: 0;
    color: var(--ink);
    font-weight: 400;
    font-size: 46px;
    line-height: 54px;
  }
  .tagline {
    position: absolute;
    top: 400px;
    left: 76px;
    width: 600px;
    text-align: center;
    margin: 0;
    color: var(--red);
    font-size: 35px;
    line-height: 46px;
    font-weight: 400;
  }
  .page-code {
    position: absolute;
    left: 556px;
    top: 1175px;
    font-size: 13px;
    color: var(--muted);
  }
</style>
</head>
<body>
  <main class="page">
    <svg class="page-art" width="720" height="1200" viewBox="0 0 720 1200">
      <defs>
        <linearGradient id="press-tones" x1="0" y1="0" x2="1" y2="1">
          <stop offset="0" stop-color="#c9d2ef"/>
          <stop offset="0.35" stop-color="#8f8aa8"/>
          <stop offset="0.6" stop-color="#b7a79a"/>
          <stop offset="0.8" stop-color="#f2823a"/>
          <stop offset="1" stop-color="#d9d4d2"/>
        </linearGradient>
      </defs>

      <rect class="spine-line" x="24" y="116" width="8" height="1084" fill="var(--blue)"/>
      <path class="spine-tab" d="M0,0 L84,0 L94,38 Q98,48 90,56 L24,122 L24,1200 L0,1200 Z" fill="var(--orange)"/>

      <circle class="brand-mark" cx="376" cy="180" r="62" fill="var(--purple)"/>

      <path class="press-photo" role="img" aria-label="Close-up photo of a printer nozzle over an orange ball"
            d="M720,508 L364,864 Q338,890 362,918 L608,1200 L720,1200 Z" fill="url(#press-tones)"/>

      <rect class="tile tile-purple" x="251" y="742" width="126" height="126" rx="10" transform="rotate(45 314 805)" fill="var(--purple)"/>
      <rect class="tile tile-green" x="153" y="846" width="126" height="126" rx="10" transform="rotate(45 216 909)" fill="var(--green)"/>
      <rect class="tile tile-red" x="252" y="950" width="126" height="126" rx="10" transform="rotate(45 315 1013)" fill="var(--red)"/>
    </svg>

    <h1 class="brand">Quill Press<br>Oceania</h1>
    <p class="tagline">Specialist producing quality<br>printed books to your deadline</p>
    <span class="page-code">C6</span>
  </main>
</body>
</html>
```